Stationery Design Task - Stationary, memo and report templates for professional services company

Looking for someone to update stationary design but just as importantly come up with a template for reports and memos for use in our consulting firm. Would also like some brand use guidelines to be able to share with our whole team. We have an existing logo that we like. Need to update with a more contemporary look so that our deliverables to clients look good and professional yet stylish. This is for business to business communications. No need for envelope design. Important to have design for multiple pages, i.e. first page of a report and then 2nd page. Need to use in MS word documents so must be easy to use and replicate. Don't want something overly complex. Clean, fresh looking is best.

Industry/Entity Type

Information Technology

Font styles to use
Sans Serif

Colors
33a6d7
0792cd
85cae6
cee9f5
cedeed
85abd2
3377b5
0455a3

Requirements
Must have
• Clean look but with a little style or pop. Something that can easily be used in word documents. Need to have page styles that have a first page of a report (not a cover page) and then secondary page.
Nice to have
• - Although the dark blue is our primary color. Might be willing to look at some accent color as well.
Should not have
• Not just our logo on the page with a color bar.

```html
<!DOCTYPE html>
<html lang="en">
<head>
<meta charset="utf-8">
<title>Meridian Systems Letterhead</title>
<link href="https://fonts.googleapis.com/css2?family=Open+Sans:wght@400;700&display=swap" rel="stylesheet">
<style>
  :root {
    --backdrop: #d9d9d9;
    --paper: #ffffff;
    --cyan: #12d6f2;
    --sky: #33a6d7;
    --brand: #0792cd;
    --deep: #0455a3;
    --text-grey: #6a6a6a;
    --watermark: #efefef;
  }
  * { box-sizing: border-box; margin: 0; padding: 0; }
  html, body { width: 1200px; height: 784px; overflow: hidden; }
  body {
    background: radial-gradient(ellipse at 50% 30%, #e6e6e6 0%, var(--backdrop) 70%);
    font-family: "Open Sans", Arial, sans-serif;
  }
  .letterhead {
    position: absolute;
    left: 346px; top: 32px;
    width: 508px; height: 720px;
    background: var(--paper);
    box-shadow: 0 6px 18px rgba(0,0,0,0.18);
    overflow: hidden;
  }
  .side-band {
    position: absolute; left: 0; top: 0;
    width: 70px; height: 720px; display: block;
  }
  .brand-tab {
    position: absolute; left: 14px; top: 54px;
    width: 210px; height: 56px;
    background: var(--paper);
    border-top-left-radius: 10px;
    display: flex; align-items: center; gap: 8px;
    padding-left: 14px;
  }
  .brand-dot { width: 16px; height: 16px; border-radius: 50%; background: var(--brand); flex: none; }
  .brand-name {
    font-weight: 700; font-size: 15px; letter-spacing: 0.4px;
    color: var(--brand); text-transform: uppercase; line-height: 1;
    white-space: nowrap;
  }
  .watermark {
    position: absolute; left: 72px; top: 214px;
    width: 330px; height: 300px;
    border-radius: 50%;
    background: radial-gradient(ellipse at 55% 45%, var(--watermark) 0%, #f3f3f3 50%, rgba(255,255,255,0) 72%);
  }
  .contact {
    position: absolute; left: 76px; top: 670px;
    font-size: 7.5px; line-height: 12px; color: var(--text-grey);
  }
  .contact-line { display: flex; align-items: center; gap: 4px; white-space: nowrap; }
  .contact-line .icon {
    width: 7px; height: 7px; border-radius: 50%; background: var(--brand); flex: none;
  }
  .contact-line .icon + .icon, .contact-line .gap { margin-left: 3px; }
  .contact-line.address { color: var(--brand); font-weight: 700; }
</style>
</head>
<body>
  <main class="letterhead">
    <svg class="side-band" viewBox="0 0 70 720" aria-hidden="true">
      <defs>
        <linearGradient id="bandFill" x1="0" y1="1" x2="0" y2="0">
          <stop offset="0" stop-color="#12d6f2"/>
          <stop offset="0.55" stop-color="#0fa8e0"/>
          <stop offset="1" stop-color="#0b6fc4"/>
        </linearGradient>
      </defs>
      <polygon points="0,0 39,0 66,720 0,720" fill="url(#bandFill)"/>
      <polygon points="0,420 50,560 0,640" fill="#ffffff" opacity="0.10"/>
      <polygon points="10,520 60,680 20,720" fill="#ffffff" opacity="0.08"/>
      <polygon points="0,180 44,300 0,360" fill="#0455a3" opacity="0.12"/>
      <polygon points="0,40 38,20 20,160" fill="#0455a3" opacity="0.15"/>
      <polygon points="5,600 64,700 0,720" fill="#ffffff" opacity="0.08"/>
    </svg>

    <div class="brand-tab">
      <span class="brand-dot"></span>
      <span class="brand-name">Meridian Systems</span>
    </div>

    <div class="watermark" role="img" aria-label="Faint grey background watermark"></div>

    <div class="contact">
      <div class="contact-line address"><span class="icon"></span>0000 Harbor Lane, Westbrook, OO 00003</div>
      <div class="contact-line"><span class="icon"></span>(000) 000 4100<span class="icon gap"></span>hello@meridiansystems.com</div>
      <div class="contact-line"><span class="icon"></span>www.meridiansystems.com</div>
    </div>
  </main>
</body>
</html>
```